political advertisement for magazine

9.135 in 12.125 in. My wife is running for Judge. She needs an ad for an African-American Magazine ASAP . The ad is about a testimonial by one of her clients that makes her relatable to the African-American community. I am uploading the text for the testimonial, the picture of my wife and her client, her logo, a possible backdrop and also a slogan.

Target Market(s)

This is going in a church publication geared toward the African American Community

Requirements
Nice to have
• The image of all the people in the back. On top of that image, you have "The people stand behind Delphine for Circuit Court Judge". Also you have a letter from her client with a picture of both of them. Also include the vote for Delphine logo and her headshot. The above is just my idea if you have an idea that is totally different but portrays that Delphine is for the people, I am ok with that too. thanks!

```html
<!DOCTYPE html>
<html lang="en">
<head>
<meta charset="utf-8">
<title>The People Stand Behind Delphine – Circuit Court Judge</title>
<link href="https://fonts.googleapis.com/css2?family=Open+Sans:wght@400;600;700;800&display=swap" rel="stylesheet">
<style>
  :root {
    --campaign-blue: #2356a8;
    --campaign-blue-deep: #1a4391;
    --campaign-navy: #1b3a7a;
    --campaign-red: #e8141a;
    --campaign-red-deep: #c90d12;
    --crowd-grey-light: #eeeeee;
    --crowd-grey: #c9c9c9;
    --white: #ffffff;
  }
  * { margin: 0; padding: 0; box-sizing: border-box; }
  html, body { width: 719px; height: 1200px; overflow: hidden; background: #f2f2f2; }
  body { font-family: "Open Sans", Arial, sans-serif; }

  .ad-page { position: relative; width: 719px; height: 1200px; overflow: hidden; background: var(--crowd-grey-light); }
  .ad-shapes { position: absolute; inset: 0; }

  .headline { position: absolute; left: 0; right: 0; text-align: center; color: var(--white); }
  .headline-kicker { top: 40px; font-size: 29px; font-weight: 700; letter-spacing: 0.3px; }
  .headline-office { top: 200px; font-size: 33px; font-weight: 700; letter-spacing: 0.2px; }
  .headline-rule { position: absolute; top: 252px; left: 136px; width: 447px; height: 2px; background: var(--white); }
  .disclaimer { position: absolute; top: 262px; left: 120px; width: 479px; text-align: center; color: var(--white); font-size: 11.5px; font-weight: 600; line-height: 17px; }

  .headshot {
    position: absolute; left: 0; top: 381px; width: 333px; height: 512px;
    border-radius: 150px 150px 0 0;
    background: linear-gradient(180deg, #8a5a3c 0%, #c79a7c 35%, #2a2a2a 62%, #111 100%);
  }

  .candidate-name { position: absolute; left: 340px; top: 520px; width: 360px; text-align: center; color: var(--campaign-red); font-weight: 700; }
  .candidate-first { display: block; font-size: 68px; line-height: 78px; letter-spacing: 0.5px; }
  .candidate-last { display: block; font-size: 27px; line-height: 36px; letter-spacing: 1.5px; }

  .testimonial-band { position: absolute; left: 0; top: 893px; width: 719px; height: 307px; background: var(--campaign-red); }
  .client-photo-ring {
    position: absolute; left: 22px; top: 944px; width: 208px; height: 208px;
    border-radius: 50%; border: 2px solid var(--white); padding: 8px;
  }
  .client-photo {
    width: 100%; height: 100%; border-radius: 50%;
    background: radial-gradient(circle at 45% 40%, #8fae6a 0%, #4f7a3a 45%, #b7c6cf 100%);
  }

  .quote-mark { position: absolute; color: var(--white); font-weight: 800; font-size: 58px; line-height: 1; }
  .quote-open { left: 240px; top: 920px; }
  .quote-close { left: 432px; top: 1098px; }

  .testimonial-text { position: absolute; left: 281px; top: 931px; width: 409px; color: var(--white); font-size: 11.2px; line-height: 16.2px; text-align: justify; }
  .testimonial-text p + p { margin-top: 9px; }

  .signature { position: absolute; right: 29px; top: 1124px; text-align: right; color: var(--white); font-size: 16px; line-height: 22px; }
  .signature-name { font-weight: 700; }
</style>
</head>
<body>
<main class="ad-page">
  <svg class="ad-shapes" width="719" height="1200" viewBox="0 0 719 1200" aria-hidden="false">
    <defs>
      <linearGradient id="crowdBlue" x1="0" y1="0" x2="1" y2="1">
        <stop offset="0" stop-color="#2b61b5"/>
        <stop offset="1" stop-color="#1a4391"/>
      </linearGradient>
      <linearGradient id="crowdGrey" x1="0" y1="0" x2="1" y2="1">
        <stop offset="0" stop-color="#e2e2e2"/>
        <stop offset="1" stop-color="#cfcfcf"/>
      </linearGradient>
      <linearGradient id="nameRed" x1="0" y1="0" x2="0" y2="1">
        <stop offset="0" stop-color="#ff2a2a"/>
        <stop offset="1" stop-color="#d10f14"/>
      </linearGradient>
    </defs>
    <rect x="0" y="330" width="719" height="563" fill="url(#crowdGrey)" role="img" aria-label="Grey-toned collage of smiling faces from the community"/>
    <path d="M0 0 H719 V345 C650 370 560 378 460 360 C330 336 150 318 0 336 Z" fill="url(#crowdBlue)" role="img" aria-label="Blue-tinted collage of smiling faces from the community"/>
    <path d="M0 332 C150 312 330 328 460 352 C560 370 650 364 719 332 L719 338 C650 372 560 380 460 362 C330 338 150 322 0 340 Z" fill="#ffffff" opacity="0.85"/>
    <path d="M0 340 C150 322 330 338 460 362 C560 380 650 372 719 338 L719 352 C640 400 520 422 400 406 C250 386 120 346 0 352 Z" fill="var(--campaign-red)"/>
    <text x="359.5" y="190" text-anchor="middle" font-family="Open Sans, Arial, sans-serif" font-weight="800" font-size="126" textLength="470" lengthAdjust="spacingAndGlyphs" fill="url(#nameRed)" stroke="#ffffff" stroke-width="3" paint-order="stroke">DELPHINE</text>
  </svg>

  <h1 class="headline headline-kicker">THE PEOPLE STAND BEHIND</h1>
  <h2 class="headline headline-office">FOR CIRCUIT COURT JUDGE</h2>
  <div class="headline-rule"></div>
  <p class="disclaimer">Political Advertisement paid for and approved by the Committee to Elect Delphine Ravello Lindqvist, no party affiliation, for Circuit Court Judge</p>

  <div class="headshot" role="img" aria-label="Portrait of the candidate in a black blazer and pearl necklace"></div>

  <div class="candidate-name">
    <span class="candidate-first">Delphine</span>
    <span class="candidate-last">Ravello Lindqvist</span>
  </div>

  <section class="testimonial-band">
  </section>
  <div class="client-photo-ring">
    <div class="client-photo" role="img" aria-label="Photo of the candidate shaking hands with her client in front of flowering shrubs"></div>
  </div>

  <span class="quote-mark quote-open">“</span>
  <div class="testimonial-text">
    <p>For the past few years, Delphine Ravello Lindqvist has been my lawyer. She has always strived to provide excellence in legal services. Her almost encyclopedic knowledge of the law makes for a flawless, precise, navigation of the legal system, with results.</p>
    <p>She is the epitome of professionalism, that is aptly balanced by her calm persona. Her empathy is more than commendable, and her legal experience unmatched.</p>
    <p>Delphine Ravello Lindqvist is truly one of kind, deserving of all accolades, appointments, and accomplishments.</p>
  </div>
  <span class="quote-mark quote-close">”</span>

  <div class="signature">
    <div>Yours Truly,</div>
    <div class="signature-name">Thomas Whitfield</div>
  </div>
</main>
</body>
</html>
```